Vexmor Industries - Quality Campaign

Objective:

Create a visually engaging graphic design that promotes quality awareness and engagement within Vexmor Industries. The design should convey the core values of quality at Vexmor, emphasizing its four key elements:

Zero Defects, Zero Scrap
Customer Satisfaction
First Time Right
Product Performance
Target Audience:

Vexmor Industries employees at all levels.

Usage:

The design will be used for various purposes, including:

Posters displayed in common areas and workstations
Presentation slides for internal meetings and training sessions
Design Requirements:

Visual Style: The design should be modern, professional, and visually appealing. It should evoke a sense of pride in quality and inspire team members to strive for excellence.
Color Palette: Consider using the Vexmor Industries brand colors or a complementary palette that reflects quality and professionalism (see website: https://www.vexmor-industries.example/).
Key Elements: The four key elements of quality should be clearly visible and integrated into the design. This could be achieved through text, icons, or a combination of both.
Vexmor Industries Logo: A vector file of the Vexmor Industries logo will be provided. Optional use of the logo is encouraged to maintain brand consistency.
Call to Action: The design should include a clear call to action, such as "Embrace Quality," "Strive for Excellence," or "Own Your Quality."
Additional Considerations:

Versatility: The design should be adaptable for different formats and sizes (e.g., posters, presentations, social media posts).
Memorability: The design should be memorable and easily recognizable as representing Vexmor Industries' commitment to quality.
Deliverables:

High-resolution digital files in various formats suitable for printing and digital use.
By adhering to these guidelines, the winning design will effectively communicate the importance of quality at Vexmor Industries and inspire employees to embrace these values in their daily work.

Industry/Entity Type

Engineering, manufacturing, semi-conductor, optics

Requirements
Must have
• Reference to Quality and 4 key elements

```html
<!DOCTYPE html>
<html lang="en">
<head>
<meta charset="utf-8">
<title>Vexmor Industries – Embrace Quality</title>
<link rel="stylesheet" href="https://fonts.googleapis.com/css2?family=Barlow:wght@600;700&family=Roboto:wght@500&display=swap">
<style>
  :root {
    --header-bg: #f5f7f2;
    --brand-blue: #4f82c4;
    --field-blue: #5889c7;
    --field-glow: #86a5d3;
    --white: #ffffff;
    --icon-accent: #6f98cf;
  }
  * { margin: 0; padding: 0; box-sizing: border-box; }
  html, body { width: 900px; height: 1200px; overflow: hidden; }
  body { font-family: "Barlow", Arial, sans-serif; }

  .poster { position: relative; width: 900px; height: 1200px; overflow: hidden; }

  .brand-bar {
    position: absolute; left: 0; top: 0; width: 900px; height: 122px;
    background: var(--header-bg);
  }
  .brand-mark {
    position: absolute; left: 28px; top: 28px; width: 77px; height: 77px;
    background: var(--brand-blue);
  }
  .brand-name {
    position: absolute; left: 116px; top: 26px;
    font-family: "Roboto", Arial, sans-serif; font-weight: 500;
    font-size: 33px; line-height: 36px; color: var(--brand-blue);
  }

  .campaign-field {
    position: absolute; left: 0; top: 122px; width: 900px; height: 1078px;
    background: radial-gradient(ellipse 60% 45% at 50% 48%, var(--field-glow) 0%, #7b9fd2 45%, var(--field-blue) 100%);
  }

  .award-scene {
    position: absolute; left: 150px; top: 450px; width: 590px; height: 420px;
    border-radius: 16px;
    background: linear-gradient(180deg, rgba(236,226,190,0.28) 0%, rgba(222,216,168,0.5) 100%);
  }

  .headline { color: var(--white); font-weight: 700; }
  .headline-lead {
    position: absolute; left: 103px; top: 205px;
    font-size: 92px; line-height: 1; letter-spacing: 1px; white-space: nowrap;
  }
  .headline-main {
    position: absolute; left: 100px; top: 268px;
    font-size: 222px; line-height: 1; letter-spacing: -2px; white-space: nowrap;
  }

  .pillar {
    position: absolute; top: 982px; width: 200px; margin-left: -100px;
    text-align: center; color: var(--white);
  }
  .pillar-icon { display: block; margin: 0 auto 20px; width: 42px; height: 42px; }
  .pillar-label {
    font-weight: 600; font-size: 26px; line-height: 32px; letter-spacing: 0.5px; white-space: nowrap;
  }
  .pillar-divider {
    position: absolute; top: 1023px; width: 5px; height: 116px; margin-left: -2px;
    background: var(--white); border-radius: 3px;
  }
</style>
</head>
<body>
<main class="poster">
  <header class="brand-bar">
    <span class="brand-mark"></span>
    <div class="brand-name">Vexmor<br>Industries</div>
  </header>

  <div class="campaign-field"></div>

  <div class="award-scene" role="img" aria-label="Photo of a gold first-place medal balanced on a white pedestal, with a second gold medal leaning against it on stacked pale gold discs"></div>

  <h1 class="headline">
    <span class="headline-lead">Embrace</span>
    <span class="headline-main">Quality.</span>
  </h1>

  <section class="pillars">
    <div class="pillar" style="left:154px">
      <svg class="pillar-icon" viewBox="0 0 44 44"><rect x="11" y="4" width="22" height="36" rx="5" fill="none" stroke="#fff" stroke-width="5"/></svg>
      <p class="pillar-label">Zero Defects<br>Zero Scrap</p>
    </div>
    <span class="pillar-divider" style="left:256px"></span>

    <div class="pillar" style="left:356px">
      <svg class="pillar-icon" viewBox="0 0 44 44" fill="#fff">
        <polygon points="22,2 24,7 29,7 25,10 26,15 22,12 18,15 19,10 15,7 20,7"/>
        <polygon points="8,6 9.5,9.5 13,9.5 10,12 11,15.5 8,13.5 5,15.5 6,12 3,9.5 6.5,9.5"/>
        <polygon points="36,6 37.5,9.5 41,9.5 38,12 39,15.5 36,13.5 33,15.5 34,12 31,9.5 34.5,9.5"/>
        <circle cx="22" cy="24" r="5"/><circle cx="10" cy="26" r="4"/><circle cx="34" cy="26" r="4"/>
        <path d="M13 44c0-8 4-12 9-12s9 4 9 12z"/><path d="M2 42c0-6 3-9 8-9 2 0 3 .5 4 1-2 2-3 5-3 8z"/><path d="M42 42c0-6-3-9-8-9-2 0-3 .5-4 1 2 2 3 5 3 8z"/>
      </svg>
      <p class="pillar-label">Customer<br>Satisfaction</p>
    </div>
    <span class="pillar-divider" style="left:453px"></span>

    <div class="pillar" style="left:540px">
      <svg class="pillar-icon" viewBox="0 0 44 44"><circle cx="22" cy="22" r="21" fill="#fff"/><path d="M13 22l6 6 12-12" fill="none" stroke="var(--icon-accent)" stroke-width="4" stroke-linecap="round" stroke-linejoin="round"/></svg>
      <p class="pillar-label">First Time<br>Right</p>
    </div>
    <span class="pillar-divider" style="left:635px"></span>

    <div class="pillar" style="left:745px">
      <svg class="pillar-icon" viewBox="0 0 44 44"><path d="M7 36A18 18 0 1 1 37 36" fill="none" stroke="#fff" stroke-width="6" stroke-dasharray="9 3"/><path d="M14 16l14 16" stroke="#fff" stroke-width="5" stroke-linecap="round"/></svg>
      <p class="pillar-label">Product<br>Performance</p>
    </div>
  </section>
</main>
</body>
</html>
```